Veluxa Bone & Motion Business Card

Need a business card using the logo provided. I want brand side of the card to be grey with the logo in the center of the card in white.

On the other side I leave to the designers

Target Market(s)

Personal Injury Attorneys

Industry/Entity Type

Medical

Contact Information for Business Card

Name, CEO. Cell Phone, (Fairholt, Address, Phone) (Westbrook, Address, Phone) (Ashford Lake, Address, Phone)

Colors

Designer to choose only greyscale colors for use in the design.

Requirements
Must have
• Logo by itself on one side

```html
<!DOCTYPE html>
<html lang="en">
<head>
<meta charset="utf-8">
<title>Veluxa Bone &amp; Motion – Business Card</title>
<link rel="stylesheet" href="https://fonts.googleapis.com/css2?family=Roboto:wght@300;400;500;700&display=swap">
<style>
  :root {
    --page: #ffffff;
    --card-base: #868686;
    --card-light: #a2a2a2;
    --card-dark: #7a7a7a;
    --ink-white: #ffffff;
    --ink-soft: #f1f1f1;
    --accent-bar: #6b6b6b;
    --divider: #5f5f5f;
    --art-light: #e9e9e9;
    --art-mid: #b3b3b3;
    --card-shadow: 0 2px 6px rgba(0,0,0,0.22);
  }
  * { box-sizing: border-box; margin: 0; padding: 0; }
  html, body {
    width: 687px; height: 1200px; overflow: hidden;
    background: var(--page);
    font-family: "Roboto", Arial, sans-serif;
  }
  .sheet { position: relative; width: 687px; height: 1200px; }
  .card {
    position: absolute; left: 115px; width: 446px; height: 255px;
    overflow: hidden; box-shadow: var(--card-shadow);
    background: radial-gradient(ellipse 70% 80% at 50% 40%, var(--card-light), var(--card-base) 70%, var(--card-dark));
  }
  .card--brand { top: 330px; }
  .card--contact { top: 618px; }

  /* brand side */
  .corner-art {
    position: absolute; opacity: 0.55;
    background: radial-gradient(ellipse at center, var(--art-mid), transparent 70%);
  }
  .corner-art--top-left { left: -30px; top: -30px; width: 90px; height: 80px; }
  .corner-art--bottom-left { left: -40px; bottom: -40px; width: 120px; height: 150px; }
  .corner-art--right { right: -40px; top: 20px; width: 110px; height: 200px; }

  .brand-name {
    position: absolute; left: 0; right: 0; top: 80px;
    text-align: center; color: var(--ink-white);
    font-weight: 500; line-height: 1;
  }
  .brand-name__main {
    display: block; font-size: 56px; letter-spacing: 15px; padding-left: 15px;
  }
  .brand-name__sub {
    display: block; margin-top: 12px; font-size: 25px; letter-spacing: 5px; padding-left: 5px;
  }

  /* contact side */
  .spine-art {
    position: absolute; right: 0; top: 0; width: 190px; height: 255px;
    background:
      radial-gradient(ellipse 55% 60% at 75% 45%, var(--art-light), transparent 75%),
      linear-gradient(100deg, transparent 20%, rgba(200,200,200,0.35) 60%, rgba(150,150,150,0.2));
  }
  .accent-bar {
    position: absolute; left: 0; top: 25px; width: 14px; height: 54px;
    background: var(--accent-bar);
  }
  .person { position: absolute; left: 27px; top: 24px; color: var(--ink-white); }
  .person__name { font-size: 20px; font-weight: 700; line-height: 1.05; }
  .person__title { font-size: 17px; font-weight: 300; line-height: 1.15; }
  .person__phone {
    display: flex; align-items: center; gap: 7px;
    font-size: 14px; font-weight: 400; margin-top: 2px;
  }
  .icon { flex: none; fill: none; stroke: var(--ink-white); stroke-width: 1.6; }

  .locations { position: absolute; left: 27px; top: 106px; list-style: none; }
  .location { display: flex; align-items: center; height: 48px; }
  .location__city {
    width: 65px; font-size: 10.5px; font-weight: 500; color: var(--ink-white);
    white-space: nowrap;
  }
  .location__details {
    border-left: 1px solid var(--divider); padding-left: 12px;
    color: var(--ink-soft); font-size: 9px; line-height: 1.3;
  }
  .detail { display: flex; align-items: flex-start; gap: 7px; }
  .detail--phone { font-weight: 700; color: var(--ink-white); }
  .detail .icon { width: 8px; height: 8px; margin-top: 2px; }
</style>
</head>
<body>
<main class="sheet">

  <section class="card card--brand" aria-label="Brand side">
    <div class="corner-art corner-art--top-left" role="img" aria-label="Faint spine illustration"></div>
    <div class="corner-art corner-art--bottom-left" role="img" aria-label="Faint spine illustration"></div>
    <div class="corner-art corner-art--right" role="img" aria-label="Faint spine illustration"></div>
    <h1 class="brand-name">
      <span class="brand-name__main">VELUXA</span>
      <span class="brand-name__sub">BONE &amp; MOTION</span>
    </h1>
  </section>

  <section class="card card--contact" aria-label="Contact side">
    <div class="spine-art" role="img" aria-label="3D illustration of a human spine on a lit grey backdrop"></div>
    <div class="accent-bar"></div>

    <div class="person">
      <p class="person__name">Marcus Delano</p>
      <p class="person__title">CEO</p>
      <p class="person__phone">
        <svg class="icon" width="12" height="12" viewBox="0 0 12 12"><path d="M3 1.5l1.5 2.5-1 1c.6 1.4 1.6 2.4 3 3l1-1L10 8.5 9 10.5C5 10.5 1.5 7 1.5 3z"/></svg>
        +1234 567 899
      </p>
    </div>

    <ul class="locations">
      <li class="location">
        <span class="location__city">Fairholt</span>
        <div class="location__details">
          <p class="detail detail--phone"><svg class="icon" viewBox="0 0 12 12"><path d="M3 1.5l1.5 2.5-1 1c.6 1.4 1.6 2.4 3 3l1-1L10 8.5 9 10.5C5 10.5 1.5 7 1.5 3z"/></svg>+1234 567 899</p>
          <p class="detail"><svg class="icon" viewBox="0 0 12 12"><path d="M6 11S2 7 2 4.5a4 4 0 018 0C10 7 6 11 6 11z"/><circle cx="6" cy="4.5" r="1.3"/></svg><span>Street Goes here,<br>Your address goes here</span></p>
        </div>
      </li>
      <li class="location">
        <span class="location__city">Westbrook</span>
        <div class="location__details">
          <p class="detail detail--phone"><svg class="icon" viewBox="0 0 12 12"><path d="M3 1.5l1.5 2.5-1 1c.6 1.4 1.6 2.4 3 3l1-1L10 8.5 9 10.5C5 10.5 1.5 7 1.5 3z"/></svg>+1234 567 899</p>
          <p class="detail"><svg class="icon" viewBox="0 0 12 12"><path d="M6 11S2 7 2 4.5a4 4 0 018 0C10 7 6 11 6 11z"/><circle cx="6" cy="4.5" r="1.3"/></svg><span>Street Goes here,<br>Your address goes here</span></p>
        </div>
      </li>
      <li class="location">
        <span class="location__city">Ashford Lake</span>
        <div class="location__details">
          <p class="detail detail--phone"><svg class="icon" viewBox="0 0 12 12"><path d="M3 1.5l1.5 2.5-1 1c.6 1.4 1.6 2.4 3 3l1-1L10 8.5 9 10.5C5 10.5 1.5 7 1.5 3z"/></svg>+1234 567 899</p>
          <p class="detail"><svg class="icon" viewBox="0 0 12 12"><path d="M6 11S2 7 2 4.5a4 4 0 018 0C10 7 6 11 6 11z"/><circle cx="6" cy="4.5" r="1.3"/></svg><span>Street Goes here,<br>Your address goes here</span></p>
        </div>
      </li>
    </ul>
  </section>

</main>
</body>
</html>
```